Business Card Design for Occupational Medicine Start Up Company

We need to design a professional business card. We are a healthcare company providing occupational medicine services to blue collar industries. We are professional, efficient and high quality service providers.

Target Market(s)

Blue Collar Industry: Shipbuilding, Ports, Trucking Companies; The Executives and Safety Officers for these companies

Industry/Entity Type

Healthcare

Contact Information for Business Card

Logo, Name, Title, Email, Phone

Other font styles liked:
• Please match our Brand Guide

Requirements
Must have
• Our Company Colors and Logo

```html
<!DOCTYPE html>
<html lang="en">
<head>
<meta charset="utf-8">
<title>CrewWell Business Card</title>
<link rel="stylesheet" href="https://fonts.googleapis.com/css2?family=Montserrat:wght@400;700;800&family=Roboto:wght@400;500&display=swap">
<style>
  :root {
    --navy: #2b3488;
    --navy-deep: #232c7a;
    --sky: #27a6dd;
    --amber: #f2a93b;
    --paper: #ffffff;
    --ink: #1d1f3a;
    --stage: #e7e8ec;
  }
  * { margin: 0; padding: 0; box-sizing: border-box; }
  html, body { width: 1200px; height: 912px; overflow: hidden; background: var(--stage); }
  .canvas { position: relative; width: 1200px; height: 912px; }
  .card {
    position: absolute; width: 620px; height: 354px; overflow: hidden;
    box-shadow: 0 10px 28px rgba(20, 24, 60, .22);
  }
  .card-back { left: 70px; top: 60px; background: var(--navy); }
  .card-back .pattern-area {
    position: absolute; inset: 0;
    background: radial-gradient(circle at 70% 30%, #3441a0 0%, var(--navy) 55%, var(--navy-deep) 100%);
  }
  .card-back .back-brand {
    position: absolute; right: 120px; top: 120px;
    display: flex; align-items: center; gap: 8px;
    font: 700 18px Montserrat, sans-serif; color: var(--paper); letter-spacing: .5px;
  }
  .back-brand .dot { width: 12px; height: 12px; border-radius: 50%; background: var(--sky); }
  .card-front { left: 510px; top: 488px; background: var(--paper); }
  .card-front .waves { position: absolute; inset: 0; }
  .holder { position: absolute; right: 34px; top: 38px; text-align: right; }
  .holder-name { font: 800 26px Montserrat, sans-serif; color: var(--amber); text-transform: uppercase; letter-spacing: .3px; }
  .holder-title { font: 400 14px Roboto, sans-serif; color: var(--paper); margin-top: 2px; }
  .contacts { position: absolute; right: 34px; top: 178px; text-align: right; list-style: none; }
  .contacts li {
    display: flex; justify-content: flex-end; align-items: center; gap: 6px;
    font: 400 15px Roboto, sans-serif; color: var(--ink); line-height: 22px;
  }
  .contacts svg { width: 11px; height: 11px; fill: var(--navy); }
  .brand {
    position: absolute; left: 130px; top: 268px;
    display: flex; align-items: center; gap: 12px;
    font: 700 34px Montserrat, sans-serif; color: var(--navy); letter-spacing: 1px;
  }
  .brand .dot { width: 22px; height: 22px; border-radius: 50%; background: var(--sky); }
</style>
</head>
<body>
<main class="canvas">
  <section class="card card-back">
    <div class="pattern-area" role="img" aria-label="Repeating embossed pattern of the brand symbol on navy"></div>
    <div class="back-brand"><span class="dot"></span>CrewWell</div>
  </section>

  <section class="card card-front">
    <svg class="waves" viewBox="0 0 620 354" preserveAspectRatio="none" aria-hidden="true">
      <path d="M0 0 H620 V60 C520 130 400 150 260 172 C160 188 60 215 0 250 Z" fill="var(--navy)"/>
      <path d="M0 250 C60 215 160 188 260 172 C400 150 520 130 620 60 V70 C520 142 400 164 270 184 C170 200 70 230 0 272 Z" fill="var(--sky)"/>
      <path d="M0 272 C70 230 170 200 270 184 L280 184 C180 202 80 240 20 300 L0 320 Z" fill="var(--amber)"/>
      <path d="M0 320 L20 300 C80 240 180 202 280 184 C180 206 90 246 30 310 L0 340 Z" fill="var(--paper)"/>
    </svg>
    <div class="holder">
      <p class="holder-name">Martin Hale</p>
      <p class="holder-title">Director</p>
    </div>
    <ul class="contacts">
      <li>(555)014 2286 <svg viewBox="0 0 12 12"><path d="M2 1h3l1 3-2 1c1 2 2 3 3 3l1-2 3 1v3c-6 0-9-4-9-9z"/></svg></li>
      <li>info@crewwell.com <svg viewBox="0 0 12 12"><path d="M0 2h12v8H0z M1 3l5 4 5-4" stroke="#fff" stroke-width="1"/></svg></li>
      <li>www.crewwell.com <svg viewBox="0 0 12 12"><circle cx="6" cy="6" r="6"/></svg></li>
    </ul>
    <div class="brand"><span class="dot"></span>CREWWELL</div>
  </section>
</main>
</body>
</html>
```